Business card design for Automotive workshop

We need a business card for a new automotive repair and tyre shop called Keelstone Prime Automotive located in New Zealand. We are a clean, modern and fresh workshop and company.

Front needs to feature logo,
my name:
Marlo Fenwicke (director)

Address:
48 Tarn Lane
Harrowmere 3592

Phone: 07 594 2713
Mobile: 027 451 9362
Email: office@keelstoneautomotive.example.nz
Website: keelstoneautomotive.example.nz

Back needs to feature an area to write down appointment details, date and time.

Also feature a list of jobs and work we do such as,
Vehicle Servicing
All Mechanical Repairs
Warrant of Fitness
Tyres & Wheel Alignments
Automotive Diagnostics
Automotive Parts & Supplies

```html
<!DOCTYPE html>
<html lang="en">
<head>
<meta charset="utf-8">
<title>Keelstone Prime Automotive – Business Card</title>
<link rel="stylesheet" href="https://fonts.googleapis.com/css2?family=Roboto:wght@400;500;700&display=swap">
<style>
  :root {
    --stage: #3b3b3b;
    --stage-light: #555555;
    --navy: #0a1730;
    --red: #e3202a;
    --white: #ffffff;
    --ink: #111111;
  }
  * { margin: 0; padding: 0; box-sizing: border-box; }
  html, body { width: 1200px; height: 750px; overflow: hidden; }
  body {
    background: radial-gradient(ellipse at 50% 40%, var(--stage-light), var(--stage) 70%);
    font-family: "Roboto", Arial, sans-serif; position: relative;
  }

  .card {
    position: absolute; top: 186px; width: 558px; height: 328px;
    border-radius: 32px; overflow: hidden; background: var(--navy);
    box-shadow: 0 4px 14px rgba(0,0,0,.45);
  }
  .card--front { left: 38px; }
  .card--back { left: 610px; }

  .front__panel { position: absolute; left: 0; top: 0; width: 269px; height: 100%; background: var(--white); }
  .front__divider { position: absolute; left: 269px; top: 0; width: 10px; height: 100%; background: var(--red); }

  .name-tab { position: absolute; left: 0; top: 70px; width: 46px; height: 28px; background: var(--red); border-radius: 0 14px 14px 0; }
  .name-icon { position: absolute; left: 24px; top: 71px; }
  .person__name { position: absolute; left: 52px; top: 69px; font-size: 24px; font-weight: 700; color: var(--ink); letter-spacing: .6px; white-space: nowrap; }
  .person__role { position: absolute; left: 46px; top: 100px; font-size: 19px; color: var(--ink); white-space: nowrap; }

  .contact { position: absolute; left: 0; height: 16px; }
  .contact__bar { position: absolute; left: 0; top: 1px; width: 34px; height: 14px; background: var(--red); }
  .contact__icon { position: absolute; left: 20px; top: -1px; }
  .contact__text { position: absolute; left: 39px; top: -1px; white-space: nowrap; font-size: 14.5px; color: var(--ink); line-height: 18px; }
  .contact__text--long { font-size: 12.6px; }

  .brand { position: absolute; text-align: center; color: var(--red); font-weight: 700; font-size: 19px; line-height: 22px; letter-spacing: 1.5px; transform: translate(-50%, -50%); white-space: nowrap; }
  .card--front .brand { left: 418px; top: 164px; }
  .card--back .brand { left: 410px; top: 163px; }

  .band { position: absolute; left: 0; width: 100%; height: 9px; background: var(--red); }
  .band--top { top: 14px; }
  .band--bottom { top: 308px; }

  .services { list-style: none; }
  .services li, .appointment__label {
    position: absolute; left: 27px; color: var(--white); font-size: 15.5px; line-height: 18px; padding-left: 12px; white-space: nowrap; transform: translateY(-50%);
  }
  .appointment__label { font-size: 14.5px; }
  .services li::before, .appointment__label::before {
    content: ""; position: absolute; left: 0; top: 6px; width: 8px; height: 8px; border-radius: 50%; background: var(--red);
  }
  .appointment__line { position: absolute; height: 3px; background: var(--white); top: 292px; }
</style>
</head>
<body>

<section class="card card--front" aria-label="Business card front">
  <div class="front__panel"></div>
  <div class="front__divider"></div>

  <div class="name-tab"></div>
  <svg class="name-icon" width="26" height="26" viewBox="0 0 26 26" aria-hidden="true">
    <circle cx="13" cy="13" r="12" fill="#111"/>
    <circle cx="13" cy="8" r="3" fill="#e3202a"/>
    <rect x="10" y="12" width="6" height="9" rx="1.5" fill="#e3202a"/>
  </svg>
  <h1 class="person__name">Marlo Fenwicke</h1>
  <p class="person__role">(Managing director)</p>

  <div class="contact" style="top:170px">
    <span class="contact__bar"></span>
    <svg class="contact__icon" width="18" height="18" viewBox="0 0 18 18" aria-hidden="true"><circle cx="9" cy="9" r="8.5" fill="#111"/><path d="M6 4.5c-1 .6-1.5 1.6-1 3 .9 2.6 2.8 4.6 5.4 5.6 1.3.5 2.3 0 3-1l-1.8-1.6-1.3.7c-1.2-.6-2.2-1.6-2.8-2.8l.7-1.3z" fill="#fff"/></svg>
    <span class="contact__text">027 451 9362</span>
  </div>
  <div class="contact" style="top:196px">
    <span class="contact__bar"></span>
    <svg class="contact__icon" width="18" height="18" viewBox="0 0 18 18" aria-hidden="true"><circle cx="9" cy="9" r="8.5" fill="#111"/><rect x="4.5" y="8" width="9" height="5" rx="1" fill="#fff"/><path d="M4 8c0-3 10-3 10 0" stroke="#fff" stroke-width="1.6" fill="none"/></svg>
    <span class="contact__text">07 594 2713</span>
  </div>
  <div class="contact" style="top:220px">
    <span class="contact__bar"></span>
    <svg class="contact__icon" width="18" height="18" viewBox="0 0 18 18" aria-hidden="true"><circle cx="9" cy="9" r="8.5" fill="#111"/><rect x="4.5" y="6" width="9" height="6.5" fill="#fff"/><path d="M4.5 6l4.5 3.5L13.5 6" stroke="#111" stroke-width="1" fill="none"/></svg>
    <span class="contact__text contact__text--long">office@keelstoneautomotive.example.nz</span>
  </div>
  <div class="contact" style="top:243px">
    <span class="contact__bar"></span>
    <svg class="contact__icon" width="18" height="18" viewBox="0 0 18 18" aria-hidden="true"><circle cx="9" cy="9" r="8.5" fill="#111"/><circle cx="9" cy="9" r="5" stroke="#fff" stroke-width="1.2" fill="none"/><ellipse cx="9" cy="9" rx="2" ry="5" stroke="#fff" stroke-width="1" fill="none"/><path d="M4 9h10" stroke="#fff" stroke-width="1"/></svg>
    <span class="contact__text contact__text--long">keelstoneautomotive.example.nz</span>
  </div>
  <div class="contact" style="top:268px">
    <span class="contact__bar"></span>
    <svg class="contact__icon" width="18" height="18" viewBox="0 0 18 18" aria-hidden="true"><circle cx="9" cy="9" r="8.5" fill="#111"/><path d="M4 9l5-4.5L14 9h-1.5v4h-7V9z" fill="#fff"/></svg>
    <span class="contact__text">48 Tarn Lane Harrowmere 3592</span>
  </div>

  <div class="brand">KEELSTONE PRIME<br>AUTOMOTIVE</div>
</section>

<section class="card card--back" aria-label="Business card back">
  <div class="band band--top"></div>

  <ul class="services">
    <li style="top:131px">Vehicle Servicing</li>
    <li style="top:159px">All Mechanical Repairs</li>
    <li style="top:179px">Warrant of Fitness</li>
    <li style="top:202px">Tyres &amp; Wheel Alignments</li>
    <li style="top:227px">Automotive Parts &amp; Supplies</li>
    <li style="top:251px">Automotive Diagnostics</li>
  </ul>

  <span class="appointment__label" style="top:291px">Date</span>
  <span class="appointment__line" style="left:75px; width:181px"></span>
  <span class="appointment__label" style="top:291px; left:292px">Time</span>
  <span class="appointment__line" style="left:342px; width:181px"></span>

  <div class="brand">KEELSTONE PRIME<br>AUTOMOTIVE</div>

  <div class="band band--bottom"></div>
</section>

</body>
</html>
```